Card Design for my dog training business Brightpaw Obedience

Need a business card design for my dog training business with my new logo. Want the card to come off professional yet fun. Want it to be very eye catchy as well. I normally have these at vet clinics, pet stores, and groomers. so need it to look better than my competitors.
Target Market(s)
dog owners
Industry/Entity Type
Dog Training
Contact Information for Business Card
needs logo, my name and info
Font styles to use
Serif
Colors
0255a3
ffffff
ec1f27
000000
333333
fbfbfb
Requirements
Must have
- Brightpaw Obedience
- Felix Orland
- 415 903 2276
- info@brightpawobedience.example
- www.brightpawobedience.example

```html
<!DOCTYPE html>
<html lang="en">
<head>
<meta charset="utf-8">
<title>Brightpaw Obedience – Business Card</title>
<link rel="stylesheet" href="https://fonts.googleapis.com/css2?family=EB+Garamond:ital,wght@0,400;0,500;1,400&family=Roboto:wght@300&display=swap">
<style>
  :root {
    --page: #e8e8e8;
    --card: #18191b;
    --card-edge: #101112;
    --ink: #c9c9c9;
    --ink-soft: #b8b8b8;
    --rule: #bfbfbf;
  }
  * { box-sizing: border-box; margin: 0; padding: 0; }
  html, body {
    width: 1125px;
    height: 1200px;
    overflow: hidden;
    background: var(--page);
  }
  .card {
    position: absolute;
    left: 150px;
    width: 825px;
    height: 471px;
    background: linear-gradient(160deg, #1c1d1f 0%, var(--card) 55%, var(--card-edge) 100%);
  }
  .card--front { top: 98px; }
  .card--back { top: 631px; }
  .card__frame {
    position: absolute;
    inset: 17px;
    border: 1.5px solid var(--rule);
  }

  /* Front */
  .brand {
    position: absolute;
    inset: 0;
    display: flex;
    flex-direction: column;
    align-items: center;
    justify-content: center;
    gap: 22px;
  }
  .brand__dot {
    width: 46px;
    height: 46px;
    border-radius: 50%;
    background: var(--ink);
  }
  .brand__name {
    font-family: "EB Garamond", serif;
    font-weight: 400;
    font-size: 40px;
    letter-spacing: 3px;
    text-transform: uppercase;
    color: var(--ink);
  }

  /* Back */
  .identity {
    position: absolute;
    top: 186px;
    left: 0;
    right: 0;
    display: flex;
    justify-content: center;
    align-items: center;
  }
  .identity__name {
    font-family: "EB Garamond", serif;
    font-weight: 500;
    font-size: 28px;
    letter-spacing: 1.5px;
    text-transform: uppercase;
    color: var(--ink);
    padding-right: 24px;
  }
  .identity__divider {
    width: 1.5px;
    height: 76px;
    background: var(--rule);
  }
  .contact {
    list-style: none;
    padding-left: 26px;
    display: flex;
    flex-direction: column;
    gap: 5px;
  }
  .contact__item {
    display: flex;
    align-items: center;
    gap: 9px;
    font-family: "Roboto", sans-serif;
    font-weight: 300;
    font-size: 19px;
    color: var(--ink-soft);
    line-height: 21px;
  }
  .contact__icon { width: 17px; height: 17px; flex: none; }
  .tagline {
    position: absolute;
    top: 360px;
    left: 0;
    right: 0;
    text-align: center;
    font-family: "EB Garamond", serif;
    font-style: italic;
    font-size: 29px;
    color: var(--ink-soft);
  }
</style>
</head>
<body>
  <section class="card card--front">
    <div class="card__frame"></div>
    <div class="brand">
      <span class="brand__dot"></span>
      <span class="brand__name">Brightpaw Obedience</span>
    </div>
  </section>

  <section class="card card--back">
    <div class="card__frame"></div>
    <div class="identity">
      <span class="identity__name">Felix Orland</span>
      <span class="identity__divider"></span>
      <ul class="contact">
        <li class="contact__item">
          <svg class="contact__icon" viewBox="0 0 24 24" aria-hidden="true"><path fill="#c9c9c9" d="M6.6 10.8a15.1 15.1 0 0 0 6.6 6.6l2.2-2.2c.3-.3.7-.4 1-.2 1.1.4 2.3.6 3.6.6.6 0 1 .4 1 1V20c0 .6-.4 1-1 1A17 17 0 0 1 3 4c0-.6.4-1 1-1h3.5c.6 0 1 .4 1 1 0 1.3.2 2.5.6 3.6.1.3 0 .7-.2 1z"/></svg>
          415 903 2276
        </li>
        <li class="contact__item">
          <svg class="contact__icon" viewBox="0 0 24 24" aria-hidden="true"><rect x="2" y="5" width="20" height="14" rx="1.5" fill="#c9c9c9"/><path d="M3 6.5l9 6.5 9-6.5" fill="none" stroke="#18191b" stroke-width="1.6"/></svg>
          info@brightpawobedience.example
        </li>
        <li class="contact__item">
          <svg class="contact__icon" viewBox="0 0 24 24" aria-hidden="true"><circle cx="12" cy="12" r="10" fill="#c9c9c9"/><path d="M2 12h20M12 2c3 3 3 17 0 20M12 2c-3 3-3 17 0 20" fill="none" stroke="#18191b" stroke-width="1.4"/></svg>
          brightpawobedience.example
        </li>
      </ul>
    </div>
    <p class="tagline">“Building good manners one happy dog at a time.”</p>
  </section>
</body>
</html>
```